Dental Practice Website design

Design a new website for Brambleford Dental Practice.
Design should be warm, neutral in colour, with some small amount of bright colour if needed but kept to a minimum. Website should look professional, high end. Home page should be easy to navigate and simple for patients to be able to book online.
Logo in files along with some examples of websites that we like. Please ask if any further info needed.
Menu should have:
About
New Patients
Treatments
Fees
Contact Us

Industry/Entity Type

Dentistry

Number of Pages Required

4 page

Font styles to use
Sans Serif

Colors

Designer to choose colors to be used in the design.

Requirements
Must have
• Ravelle ratings badge, book online button,
Nice to have
• neutral, relaxing colours
Should not have
• harsh, bright colours!

```html
<!DOCTYPE html>
<html lang="en">
<head>
<meta charset="utf-8">
<title>Brambleford Dental Practice</title>
<link href="https://fonts.googleapis.com/css2?family=Lexend:wght@500;600&family=Lato:wght@300;400;700&display=swap" rel="stylesheet">
<style>
:root{
  --green:#0d6a56;
  --green-dark:#0a5a49;
  --green-soft:#1b7a64;
  --mint:#6fe3bd;
  --mint-soft:#e3f4ef;
  --ink:#1b1d1d;
  --muted:#7a7f7e;
  --white:#ffffff;
}
*{box-sizing:border-box;margin:0;padding:0}
html,body{width:1200px;height:3266px;overflow:hidden;background:var(--white)}
body{position:relative;font-family:"Lato",sans-serif;color:var(--ink)}
.abs{position:absolute}
h1,h2,h3,.display{font-family:"Lexend",sans-serif;font-weight:600;letter-spacing:-.5px}
.accent{color:var(--green)}
.btn{position:absolute;display:flex;align-items:center;justify-content:center;gap:8px;border-radius:7px;font-size:17px;font-family:"Lato",sans-serif}
.btn-solid{background:var(--green);color:var(--white)}
.btn-outline{border:1.5px solid var(--green);color:var(--green);background:var(--white)}

/* header + hero */
.hero-bg{left:0;top:0;width:1200px;height:600px;background:linear-gradient(180deg,#e6f5f1 0%,#f3fbf9 55%,#ffffff 100%)}
.brand{display:flex;align-items:center;gap:12px}
.brand-mark{width:30px;height:30px;border:2px solid var(--green);border-radius:4px}
.brand-name{font-size:15px;line-height:18px;color:var(--ink)}
.nav{left:376px;top:46px;display:flex;gap:27px;font-size:15px;color:var(--muted)}
.nav .active{color:var(--green);font-weight:700}
.hero-title{left:110px;top:198px;font-size:64px;line-height:64px;color:var(--ink)}
.hero-sub{left:112px;top:353px;width:460px;font-size:20px;line-height:31px;color:var(--muted);font-weight:300}
.portrait-ring{left:671px;top:133px;width:344px;height:344px;border:2px solid var(--green);border-radius:50%;opacity:.8}
.portrait{left:695px;top:157px;width:296px;height:296px;border-radius:50%;background:radial-gradient(circle at 55% 40%,#c49c84 0%,#7b4f38 35%,var(--green) 62%)}
.float-icon{width:54px;height:54px;border-radius:50%;background:var(--white);box-shadow:0 6px 16px rgba(0,0,0,.1);display:flex;align-items:center;justify-content:center}
.stats{left:618px;top:433px;width:326px;height:89px;background:var(--white);border-radius:6px;box-shadow:0 10px 30px rgba(13,106,86,.1);display:flex;padding:16px 26px;gap:34px}
.stat-num{font-family:"Lexend",sans-serif;font-weight:600;font-size:31px;color:var(--green);line-height:34px}
.stat-label{font-size:14px;color:var(--muted);margin-top:4px}
.stars{color:#f5c518;font-size:14px;margin-left:6px}

/* about */
.about-photo{left:111px;top:694px;width:454px;height:573px;border-radius:4px;background:linear-gradient(135deg,#d9e4ea 0%,#8fb6d6 45%,#e8eef2 100%)}
.sec-title{font-size:42px;color:var(--ink)}
.about-intro{left:617px;top:756px;width:445px;font-size:18px;line-height:34px;color:#555;font-weight:300}
.feature{left:617px;width:470px;display:flex;gap:20px;padding:18px 16px;border-radius:6px}
.feature.card{background:var(--white);box-shadow:0 8px 26px rgba(0,0,0,.07)}
.feature-icon{flex:none;width:58px;height:58px;border-radius:6px;background:var(--mint-soft);display:flex;align-items:center;justify-content:center}
.feature p{font-size:16.5px;line-height:30px;color:var(--green);opacity:.85}

/* team */
.team-intro{left:111px;top:1500px;width:660px;font-size:18px;line-height:34px;color:#555;font-weight:300}
.member{width:297px;height:328px;background:var(--white);border-radius:6px;box-shadow:0 6px 22px rgba(0,0,0,.08);text-align:center}
.member-photo{margin:18px 18px 0;height:215px;border-radius:3px;background:linear-gradient(180deg,#eef1f4 0%,#dfe5ea 100%)}
.member h3{margin-top:18px;font-size:21px;color:var(--green)}
.member span{display:block;margin-top:10px;font-size:15px}
.dots{left:543px;top:2008px;display:flex;gap:11px}
.dots i{width:9px;height:9px;border-radius:50%;background:#d9d9d9}
.dots i.on{background:var(--green)}

/* join */
.perk{width:137px;height:152px;background:var(--white);border-radius:6px;box-shadow:0 6px 22px rgba(0,0,0,.08);text-align:center;font-size:13.5px;line-height:20px;padding-top:20px}
.perk .feature-icon{margin:0 auto 14px}
.join-text{left:618px;top:2262px;width:470px;font-size:18px;line-height:34.5px;color:#555;font-weight:300}

/* cta */
.cta{left:0;top:2505px;width:1200px;height:413px;background:var(--green-dark)}
.cta h2{position:absolute;left:0;top:80px;width:1200px;text-align:center;font-size:44px;color:var(--white)}
.cta .hl{color:var(--mint)}
.cta-art{position:absolute;left:343px;top:148px;width:110px;height:90px;border-radius:45px;background:var(--green-soft)}
.cta-sub{position:absolute;left:481px;top:180px;font-size:34px;color:var(--white)}
.cta .btn{left:476px;top:284px;width:247px;height:42px;background:var(--white);color:var(--green);font-size:16px}

/* footer */
.footer-about{left:111px;top:3058px;width:300px;font-size:14.5px;line-height:31px;color:#444}
.footer-col{top:3016px}
.footer-col h4{font-size:17px;color:var(--green);font-weight:700;margin-bottom:20px}
.footer-col li{list-style:none;font-size:14.5px;line-height:31px;color:#555}
.social{display:flex;gap:10px}
.social i{width:18px;height:18px;border-radius:4px;background:var(--green)}
.copyright{left:0;top:3219px;width:1200px;text-align:center;font-size:13px;color:#666}
</style>
</head>
<body>

<div class="abs hero-bg"></div>

<header>
  <div class="abs brand" style="left:112px;top:36px">
    <span class="brand-mark"></span>
    <span class="brand-name">BRAMBLEFORD<br>Dental practice</span>
  </div>
  <nav class="abs nav">
    <span class="active">Home</span><span>About</span><span>New Patients</span><span>Treatments</span><span>Fees</span><span>Contact</span>
  </nav>
  <a class="btn btn-outline" style="left:900px;top:34px;width:187px;height:44px">Book Appointment</a>
</header>

<section class="hero">
  <h1 class="abs hero-title">Your <span class="accent">Smile</span><br><span class="accent">Our</span> Priority</h1>
  <p class="abs hero-sub">Welcome to our friendly dental practice nestled in the heart of beautiful Larkhollow, UK.</p>
  <a class="btn btn-solid" style="left:111px;top:459px;width:188px;height:43px">Book Appointment</a>
  <a class="btn btn-outline" style="left:319px;top:459px;width:175px;height:43px">View Treatments</a>

  <div class="abs portrait-ring"></div>
  <div class="abs portrait" role="img" aria-label="Portrait of a smiling patient on a green circle"></div>
  <div class="abs float-icon" style="left:670px;top:180px">
    <svg width="24" height="26" viewBox="0 0 24 26"><path d="M6 1c3 0 4 1.5 6 1.5S15 1 18 1c4 0 6 3 5 8-1 4-2 6-2.5 11-.3 3-2.5 5-3.5 1-1-3.5-1.5-5-5-5s-4 1.5-5 5c-1 4-3.2 2-3.5-1C3 15 2 13 1 9 0 4 2 1 6 1z" fill="#0d6a56"/></svg>
  </div>
  <div class="abs float-icon" style="left:899px;top:124px">
    <svg width="26" height="24" viewBox="0 0 26 24"><path d="M13 23S1 15.5 1 7.5C1 3.5 4 1 7.2 1 10 1 12 3 13 5c1-2 3-4 5.8-4C22 1 25 3.5 25 7.5 25 15.5 13 23 13 23z" fill="#0d6a56"/></svg>
  </div>
  <div class="abs float-icon" style="left:973px;top:346px">
    <svg width="24" height="24" viewBox="0 0 24 24"><rect x="1" y="4" width="22" height="19" rx="2" fill="#0d6a56"/><rect x="5" y="1" width="3" height="6" fill="#0d6a56"/><rect x="16" y="1" width="3" height="6" fill="#0d6a56"/><g fill="#fff"><rect x="5" y="11" width="3" height="3"/><rect x="10.5" y="11" width="3" height="3"/><rect x="16" y="11" width="3" height="3"/><rect x="5" y="16" width="3" height="3"/><rect x="10.5" y="16" width="3" height="3"/></g></svg>
  </div>

  <div class="abs stats">
    <div><div class="stat-num">10k+</div><div class="stat-label">Happy Patients</div></div>
    <div><div class="stat-num">4.7<span class="stars">★★★★★</span></div><div class="stat-label">Ravelle Ratings &nbsp;›</div></div>
  </div>
</section>

<section class="about">
  <div class="abs about-photo" role="img" aria-label="Dentist and assistant treating a smiling patient in the dental chair"></div>
  <h2 class="abs sec-title" style="left:616px;top:690px">About <span class="accent">Us</span></h2>
  <p class="abs about-intro">Welcome to our friendly dental practice nestled in the heart of beautiful Larkhollow, UK.</p>
  <div class="abs feature card" style="top:834px">
    <div class="feature-icon"><svg width="28" height="26" viewBox="0 0 26 24"><path d="M13 23S1 15.5 1 7.5C1 3.5 4 1 7.2 1 10 1 12 3 13 5c1-2 3-4 5.8-4C22 1 25 3.5 25 7.5 25 15.5 13 23 13 23z" fill="#0d6a56"/></svg></div>
    <p>At our practice, we believe that a visit to the dentist should be acomfortable and positive experience.</p>
  </div>
  <div class="abs feature" style="top:962px">
    <div class="feature-icon"><svg width="28" height="28" viewBox="0 0 28 28"><path d="M2 12l7-7 5 3 5-3 7 7-9 10H11z" fill="#0d6a56"/></svg></div>
    <p>We create a warm, welcoming atmosphere where patients feel at ease and confident in their dental care.</p>
  </div>
  <div class="abs feature" style="top:1078px">
    <div class="feature-icon"><svg width="26" height="28" viewBox="0 0 24 26"><path d="M6 1c3 0 4 1.5 6 1.5S15 1 18 1c4 0 6 3 5 8-1 4-2 6-2.5 11-.3 3-2.5 5-3.5 1-1-3.5-1.5-5-5-5s-4 1.5-5 5c-1 4-3.2 2-3.5-1C3 15 2 13 1 9 0 4 2 1 6 1z" fill="#0d6a56"/></svg></div>
    <p>Our state-of-the-art facilities ensure you receive the latest techniques and treatments for optimal oral health.</p>
  </div>
  <a class="btn btn-solid" style="left:620px;top:1216px;width:153px;height:45px">Learn More
    <svg width="15" height="15" viewBox="0 0 16 16"><circle cx="8" cy="8" r="8" fill="#fff"/><path d="M6 4l4 4-4 4" stroke="#0d6a56" stroke-width="2" fill="none"/></svg></a>
</section>

<section class="team">
  <h2 class="abs sec-title" style="left:110px;top:1428px">Meet our <span class="accent">Team</span></h2>
  <p class="abs team-intro">We are delighted to introduce you to our experienced and compassionate dental team. Our team comprises highly skilled dental professionals who are dedicated to providing you with high-quality dental care services.</p>
  <a class="btn btn-outline" style="left:940px;top:1505px;width:147px;height:43px">Get in Touch</a>

  <article class="abs member" style="left:111px;top:1642px">
    <div class="member-photo" role="img" aria-label="Portrait of the prosthodontist in a white coat"></div>
    <h3>Marisa Vaughn</h3><span>Prosthodontist</span>
  </article>
  <article class="abs member" style="left:452px;top:1642px">
    <div class="member-photo" role="img" aria-label="Portrait of the periodontist holding dental tools"></div>
    <h3>Julian Ashcombe</h3><span>Periodontist</span>
  </article>
  <article class="abs member" style="left:792px;top:1642px">
    <div class="member-photo" role="img" aria-label="Portrait of the orthodontist in a white coat"></div>
    <h3>Sienna Whitlow</h3><span>Orthodontist</span>
  </article>
  <div class="abs dots"><i class="on"></i><i></i><i></i><i></i><i></i><i></i></div>
</section>

<section class="join">
  <div class="abs perk" style="left:111px;top:2189px">
    <div class="feature-icon"><svg width="28" height="26" viewBox="0 0 26 24"><path d="M13 23S1 15.5 1 7.5C1 3.5 4 1 7.2 1 10 1 12 3 13 5c1-2 3-4 5.8-4C22 1 25 3.5 25 7.5 25 15.5 13 23 13 23z" fill="#0d6a56"/></svg></div>
    Complete<br>All- Round Care
  </div>
  <div class="abs perk" style="left:267px;top:2189px">
    <div class="feature-icon"><svg width="28" height="28" viewBox="0 0 28 28"><circle cx="14" cy="14" r="4" fill="#0d6a56"/><g stroke="#0d6a56" stroke-width="2"><path d="M14 10V3M14 18v7M10 14H3M18 14h7"/></g><g fill="#0d6a56"><circle cx="14" cy="3" r="2.5"/><circle cx="14" cy="25" r="2.5"/><circle cx="3" cy="14" r="2.5"/><circle cx="25" cy="14" r="2.5"/></g></svg></div>
    Industry Latest<br>Techniques
  </div>
  <div class="abs perk" style="left:421px;top:2189px">
    <div class="feature-icon"><svg width="28" height="28" viewBox="0 0 28 28"><circle cx="17" cy="9" r="7" fill="#0d6a56"/><path d="M2 20l6-3h7l7-3 4 2-10 8H2z" fill="#0d6a56"/></svg></div>
    Quality at<br>Affordable Price
  </div>
  <a class="btn btn-solid" style="left:261px;top:2377px;width:147px;height:43px">Join Practice</a>
  <h2 class="abs sec-title" style="left:617px;top:2180px">Join Our <span class="accent">Practice</span></h2>
  <p class="abs join-text">If you're looking for an exceptional dental practice, we're here to help! Our team is made up of highly skilled professionals who are dedicated to ensuring that all our patients receive top-notch care in a welcoming and comfortable environment.</p>
</section>

<section class="abs cta">
  <h2>Book an <span class="hl">Appointment</span> Now</h2>
  <div class="cta-art" role="img" aria-label="Line illustration of a bright smile with sparkles"></div>
  <div class="cta-sub display">Your <span class="hl">Smile</span> Matters to Us</div>
  <a class="btn">Book an Appointment Now</a>
</section>

<footer>
  <div class="abs brand" style="left:112px;top:3005px">
    <span class="brand-mark"></span>
    <span class="brand-name">BRAMBLEFORD<br>Dental practice</span>
  </div>
  <p class="abs footer-about">We are passionate about improving dental health and helping you achieve your brightest smile and are honoured that you're considering us for your dental needs.</p>
  <div class="abs footer-col" style="left:555px"><h4>Explore</h4><ul><li>About Us</li><li>New Patients</li><li>Treatments</li><li>Fees</li></ul></div>
  <div class="abs footer-col" style="left:770px"><h4>Useful links</h4><ul><li>Privacy</li><li>Support</li><li>Licenses</li><li>Cookies</li></ul></div>
  <div class="abs footer-col" style="left:984px"><h4>Follow us</h4><div class="social"><i></i><i></i><i></i><i></i></div></div>
  <p class="abs copyright">© Copyright 2025 Brambleford Dental Practice All rights reserved.</p>
</footer>

</body>
</html>
```